i need a business card for a plumbing company in california

we are a drain cleaning , maintenance plumbing company who is starting new marketing campaign for a tatrench-less pipe installation department .

Target Market(s)

the professional who appreciates time and quality workmanship.

Industry/Entity Type

Plumbing

Colors
0655a3
ec1f27

Requirements
Must have
• the second logo needs to be included
Nice to have
• a focus on the services offered
Should not have
• any underlined words on the brief

```html
<!DOCTYPE html>
<html lang="en">
<head>
<meta charset="utf-8">
<title>Clearline Plumbing – Business Card</title>
<link href="https://fonts.googleapis.com/css2?family=Exo+2:wght@600;700&family=Arimo:wght@400;700&display=swap" rel="stylesheet">
<style>
  :root {
    --stage: #000000;
    --card-white: #ffffff;
    --brand-red: #dd242a;
    --brand-grey: #707068;
    --ink: #222222;
    --rule: #c4c4c4;
  }
  * { margin: 0; padding: 0; box-sizing: border-box; }
  html, body { width: 1200px; height: 900px; overflow: hidden; background: var(--stage); }
  .canvas { position: relative; width: 1200px; height: 900px; background: var(--stage); }

  .card { position: absolute; top: 275px; width: 477px; height: 293px; overflow: hidden; }
  .card-front { left: 116px; background: var(--card-white); border-radius: 0 52px 0 52px; }
  .card-back { left: 622px; background: var(--brand-red); border-radius: 52px 0 52px 0; }

  .brand-lockup {
    position: absolute; right: 26px; top: 56px;
    display: flex; align-items: center; gap: 12px;
  }
  .brand-name {
    font-family: "Exo 2", sans-serif; font-weight: 600; font-size: 33px;
    line-height: 0.98; color: var(--brand-grey); text-align: right;
  }
  .brand-square { width: 30px; height: 30px; background: var(--brand-red); }

  .person { position: absolute; left: 25px; top: 159px; font-family: "Arimo", sans-serif; }
  .person-name { font-weight: 700; font-size: 15.5px; color: var(--brand-red); letter-spacing: 0.3px; }
  .person-title { font-size: 14px; color: var(--ink); margin-top: 1px; }

  .divider { position: absolute; left: 25px; right: 26px; top: 200px; height: 1px; background: var(--rule); }

  .contact-list {
    position: absolute; left: 25px; top: 211px; list-style: none;
    font-family: "Arimo", sans-serif; font-size: 13.5px; color: var(--ink); line-height: 17.5px;
  }
  .contact-list li { display: flex; align-items: center; gap: 6px; }
  .contact-icon { width: 11px; height: 11px; fill: var(--brand-red); flex: none; }

  .address {
    position: absolute; right: 26px; top: 229px; text-align: right;
    font-family: "Arimo", sans-serif; font-size: 13.5px; color: var(--ink); line-height: 17.5px;
  }

  .back-name {
    position: absolute; left: 0; right: 0; top: 98px; padding-left: 100px;
    font-family: "Exo 2", sans-serif; font-weight: 700; font-size: 46px;
    line-height: 0.98; color: var(--card-white); text-align: right; padding-right: 118px;
  }
  .back-web {
    position: absolute; left: 0; right: 0; top: 243px; text-align: center; padding-left: 4px;
    font-family: "Arimo", sans-serif; font-size: 14px; color: var(--card-white);
  }
</style>
</head>
<body>
<main class="canvas">
  <section class="card card-front" aria-label="Business card front">
    <div class="brand-lockup">
      <p class="brand-name">Clearline<br>Plumbing</p>
      <span class="brand-square" aria-hidden="true"></span>
    </div>

    <div class="person">
      <p class="person-name">MARCUS DELGADO</p>
      <p class="person-title">Managing Director</p>
    </div>

    <div class="divider"></div>

    <ul class="contact-list">
      <li>
        <svg class="contact-icon" viewBox="0 0 12 12" aria-hidden="true"><path d="M1 4c0-2 2-3 5-3s5 1 5 3l-2 1-1-1.5H4L3 5zM2.5 6h7l1 5h-9z"/></svg>
        055-210 384 617
      </li>
      <li>
        <svg class="contact-icon" viewBox="0 0 12 12" aria-hidden="true"><path d="M3.5 0h5a1 1 0 0 1 1 1v10a1 1 0 0 1-1 1h-5a1 1 0 0 1-1-1V1a1 1 0 0 1 1-1zm.5 1.5v8h4v-8zM6 10a.6.6 0 1 0 0 1.2A.6.6 0 0 0 6 10z"/></svg>
        055-210 384 617
      </li>
      <li>
        <svg class="contact-icon" viewBox="0 0 12 12" aria-hidden="true"><path d="M0 2.5h12v7H0zm1 .8 5 3.4 5-3.4v-.1H1z"/></svg>
        hello@clearlinepipe.com
      </li>
    </ul>

    <p class="address">4820 Harbor Crest Avenue<br>Oakridge, CA 95820</p>
  </section>

  <section class="card card-back" aria-label="Business card back">
    <p class="back-name">Clearline<br>Plumbing</p>
    <p class="back-web">www.clearlinepipe.com</p>
  </section>
</main>
</body>
</html>
```